Flyer Design Project

We need a flyer design for a 1 year old domestic cleaning company based in Wiltshire, England. We provide households with high quality, hard working cleaners. We would like to see designs which use blue (the colour on the logo attatched). The final design should communicate a clean, premier and thorough service in a clear and bold way. We would like the flyer to be A5 with a single sided design. We have attached an A5 word document with the words we would like to be used in the design, what we need is for you to give it some life, colour, artwork and a professional touch. We are perfectionsists which we would like to illustrate to our customer through this flyer.
Updates

payment has been guaranteed!

Sorry..... please no pictures of females on the designs. many thanks

Target Market(s)

females with higher than average income, aged 30-50. Have families and work 9-5.

Industry/Entity Type

It Company

Requirements
Must have
• The flyer must include the logo attatched and the words in the A5 document attatched. With RELIABLE CLEANERS preferably the headline. A5 - single sided.
The Flyer must also include our introductory offer.....
First Clean FREE
Allow us to demonstrate our standards

this should be emphasised.

PLEASE NOTE: can this be added to the list of words on the flyer please:

Ironing service - one day turn around
Nice to have
• some pictures - nothing cheesey. Again, pictures should communicate our modern professional approach.

```html
<!DOCTYPE html>
<html lang="en">
<head>
<meta charset="utf-8">
<title>Brightmere Cleaners Flyer</title>
<link href="https://fonts.googleapis.com/css2?family=Caladea:wght@400;700&family=Open+Sans:wght@500;600;700&display=swap" rel="stylesheet">
<style>
  :root{
    --brand-blue:#2b6fee;
    --brand-blue-dark:#0f3fb8;
    --brand-blue-light:#5f9bff;
    --panel-grey:#e3e5e6;
    --ring-grey:#e8eaeb;
    --ink:#141414;
    --white:#ffffff;
    --bullet-gold:#d8c21a;
    --wood-dark:#4a2412;
    --wood-mid:#8a4a22;
    --wood-light:#c98a4e;
  }
  *{box-sizing:border-box;margin:0;padding:0}
  html,body{width:1200px;height:932px;overflow:hidden;background:#f2f2f2}
  .flyer{position:relative;width:1200px;height:932px;overflow:hidden;font-family:"Caladea",Georgia,serif}
  .hero-photo{position:absolute;inset:0;
    background:
      radial-gradient(ellipse 420px 380px at 1000px 420px,#5a1c1c 0%,rgba(90,28,28,.6) 45%,rgba(90,28,28,0) 75%),
      radial-gradient(ellipse 500px 160px at 420px 60px,rgba(60,60,70,.55),rgba(60,60,70,0) 70%),
      linear-gradient(170deg,var(--wood-light) 0%,var(--wood-mid) 45%,var(--wood-dark) 100%);}
  .layout-shapes{position:absolute;inset:0}
  .headline{position:absolute;color:var(--white);font-weight:400;letter-spacing:1px;line-height:1;
    text-shadow:0 2px 4px rgba(0,0,0,.55)}
  .headline--main{left:32px;top:10px;font-size:58px}
  .headline--offer{left:298px;top:84px;font-size:62px}
  .offer-note{position:absolute;left:278px;top:176px;color:var(--white);font-size:22px;letter-spacing:.5px;
    text-shadow:0 1px 3px rgba(0,0,0,.6)}
  .feature-list{position:absolute;list-style:none;color:var(--white);font-size:22px;letter-spacing:.6px;
    text-shadow:0 1px 3px rgba(0,0,0,.6)}
  .feature-list li{display:flex;align-items:center;height:34px}
  .feature-list li::before{content:"";width:12px;height:12px;border-radius:50%;margin-right:14px;
    background:radial-gradient(circle at 35% 35%,#fff59a,var(--bullet-gold) 60%,#8a7a00)}
  .feature-list--left{left:278px;top:208px}
  .feature-list--right{left:584px;top:208px}
  .ironing-badge{position:absolute;left:933px;top:143px;width:260px;height:260px}
  .ironing-badge__text{position:absolute;left:933px;top:210px;width:260px;text-align:center;color:var(--white);
    font-size:24px;line-height:31px;letter-spacing:.5px}
  .ironing-badge__text strong{font-weight:700}
  .service-photo{position:absolute;border-radius:50%;border:14px solid var(--ring-grey)}
  .service-photo--dusting{left:365px;top:320px;width:276px;height:276px;
    background:radial-gradient(circle at 40% 40%,#e2332a,#9a1610 60%,#4d2a20)}
  .service-photo--vacuum{left:712px;top:530px;width:224px;height:224px;
    background:linear-gradient(180deg,#dfe3e6 0%,#b8bec4 45%,#6a4a38 75%,#4a2f22 100%)}
  .service-photo--dishes{left:998px;top:695px;width:164px;height:164px;
    background:linear-gradient(160deg,#c8a888 0%,#e9e4de 50%,#d4d8dc 100%)}
  .brand{position:absolute;left:43px;top:650px;display:flex;align-items:center;gap:16px}
  .brand__mark{width:56px;height:56px;background:var(--brand-blue)}
  .brand__name{font-family:"Open Sans",Arial,sans-serif;font-weight:500;font-size:58px;color:var(--ink);letter-spacing:-.5px;line-height:1}
  .brand__tagline{position:absolute;left:163px;top:760px;font-family:"Open Sans",Arial,sans-serif;font-weight:600;
    font-size:29px;color:var(--ink)}
  .contact{position:absolute;top:855px;height:52px;border-radius:6px;color:var(--white);font-size:25px;
    letter-spacing:.5px;display:flex;align-items:center;justify-content:center;
    background:linear-gradient(180deg,var(--brand-blue-light) 0%,var(--brand-blue) 45%,var(--brand-blue-dark) 100%);
    box-shadow:0 2px 4px rgba(0,0,0,.35)}
  .contact--email{left:21px;width:522px}
  .contact--phone{left:549px;width:400px}
</style>
</head>
<body>
<main class="flyer">
  <div class="hero-photo" role="img" aria-label="Photo of a floor polisher working on a polished wooden floor"></div>

  <svg class="layout-shapes" width="1200" height="932" viewBox="0 0 1200 932" aria-hidden="true">
    <polygon points="0,199 1200,827 1200,932 0,932" fill="var(--brand-blue)"/>
    <polygon points="0,309 1200,849 1200,932 0,932" fill="var(--panel-grey)"/>
  </svg>

  <h1 class="headline headline--main">Reliable Cleaners!</h1>
  <h2 class="headline headline--offer">First Clean FREE</h2>
  <p class="offer-note">Allow us to demonstrate our standards......</p>

  <ul class="feature-list feature-list--left">
    <li>Personalised Service</li>
    <li>Constantly Thorough</li>
    <li>Hassel Free</li>
  </ul>
  <ul class="feature-list feature-list--right">
    <li>Insured</li>
    <li>Regular Weekly Claims</li>
    <li>No Contracts</li>
  </ul>

  <svg class="ironing-badge" viewBox="-130 -130 260 260" aria-hidden="true">
    <defs>
      <radialGradient id="badgeFill" cx="40%" cy="35%" r="70%">
        <stop offset="0" stop-color="#6aa8ff"/>
        <stop offset=".6" stop-color="#2b6fee"/>
        <stop offset="1" stop-color="#0f3fb8"/>
      </radialGradient>
    </defs>
    <polygon fill="url(#badgeFill)" points="0,-125 12,-106 29,-122 35,-101 56,-112 55,-90 78,-97 71,-76 94,-78 82,-59 104,-55 87,-40 108,-32 89,-19 110,-7 90,3 108,16 88,24 103,40 82,45 94,63 72,64 80,84 59,80 62,101 42,92 40,114 22,101 15,122 0,106 -15,122 -22,101 -40,114 -42,92 -62,101 -59,80 -80,84 -72,64 -94,63 -82,45 -103,40 -88,24 -108,16 -90,3 -110,-7 -89,-19 -108,-32 -87,-40 -104,-55 -82,-59 -94,-78 -71,-76 -78,-97 -55,-90 -56,-112 -35,-101 -29,-122 -12,-106"/>
  </svg>
  <p class="ironing-badge__text"><strong>Ironing Service</strong><br>One Day<br>Turn Around</p>

  <div class="service-photo service-photo--dusting" role="img" aria-label="Photo of a feather duster cleaning a red surface"></div>
  <div class="service-photo service-photo--vacuum" role="img" aria-label="Photo of a man vacuuming a living room floor"></div>
  <div class="service-photo service-photo--dishes" role="img" aria-label="Photo of a plate being washed at a kitchen sink"></div>

  <div class="brand">
    <span class="brand__mark" aria-hidden="true"></span>
    <span class="brand__name">Brightmere Cleaners</span>
  </div>
  <p class="brand__tagline">Premier Domestic Cleaners</p>

  <div class="contact contact--email">Email: brightmerecleaners@mailbox.co.uk</div>
  <div class="contact contact--phone">Call our hotline: 07700900418</div>
</main>
</body>
</html>
```